Ashbrook Pit Advertising / Price List

Create a 1 page document for print and email showcasing what we have available in our Quarry. Bottom of sample should have the information included and then the rest of the document focus on items and services available with the quarry. The top section will need room to list about items below and have about 5 pictures that I am working on getting.

Materials Available for Pick Up and/or Delivery:
Recycled Breaker Run
3/4" & 1 1/4" Crushed Recycled Asphalt
1 1/4" Crushed Recycled Stone
1 1/4" Screened "Dig Right On In"
3/4" Clean Stone
3/8" Washed Pea Stone
Mound Sand
Fill Sand Material
Fill/Clay Fill Material
Compost
Peot Moss
Topsoil
Reclaimed Cream City Bricks

Dumping of Materials with Approval:
Clean Concrete
Dirty and / or Large Concrete or Tolvaran
Clean Brick
Asphalt
Fill Material
Brush and / or Stumps
Hydro Vac Slurry Dumping

Target Market(s)

Contractors in our area

Industry/Entity Type

Trucking & Excavation

Colors
EB3D1F
EC4F4E
F09395
F8D3D4
FCEDEE

Requirements
Must have
• Similar Look & Feel as Sample Copy

```html
<!DOCTYPE html>
<html lang="en">
<head>
<meta charset="utf-8">
<title>Ridgeway Haulers – Materials Flyer</title>
<link rel="stylesheet" href="https://fonts.googleapis.com/css2?family=Poppins:wght@400;500;600;700;800&display=swap">
<style>
  :root {
    --red: #E9323B;
    --red-soft: #EC4F4E;
    --pink: #F09395;
    --blush: #FCEDEE;
    --green: #58B55E;
    --ink: #1E1E1E;
    --panel: #F4F4F5;
    --stage: #E8E8E9;
    --white: #FFFFFF;
  }
  * { box-sizing: border-box; margin: 0; padding: 0; }
  html, body { width: 1200px; height: 799px; overflow: hidden; }
  body { background: var(--stage); font-family: "Poppins", Arial, sans-serif; color: var(--ink); }

  .flyer {
    position: absolute; left: 330px; top: 17px;
    width: 540px; height: 764px;
    background: var(--white);
    overflow: hidden;
    box-shadow: 0 10px 30px rgba(0,0,0,.18);
  }
  .flyer__shapes { position: absolute; inset: 0; }

  .brand {
    position: absolute; left: 20px; top: 17px; width: 120px; height: 120px;
    display: flex; align-items: center; justify-content: center; text-align: center;
    color: var(--white); font-weight: 700; font-size: 14px; line-height: 1.15;
  }

  .headline {
    position: absolute; left: 25px; top: 148px;
    color: var(--white); font-weight: 700; font-size: 27px; line-height: 31px; letter-spacing: -.3px;
  }

  .section-title {
    position: absolute; font-size: 17px; line-height: 20px; font-weight: 500; color: var(--green); white-space: nowrap;
  }
  .section-title strong { color: var(--red); font-weight: 700; }
  .section-title--dumping { font-size: 17px; line-height: 18px; }

  .item {
    position: absolute; font-size: 13.5px; line-height: 16px; font-weight: 400; padding-left: 10px; white-space: nowrap;
  }
  .item b { font-weight: 600; }
  .item::before {
    content: "★"; position: absolute; left: 0; top: 0;
    color: var(--red); font-size: 8px;
  }

  .contact-bar {
    position: absolute; left: 184px; top: 682px; width: 356px; height: 52px;
    background: var(--green); border-radius: 26px 0 0 26px;
    color: var(--white); font-size: 8.4px; font-weight: 400; font-style: normal;
  }
  .contact-bar__line { position: absolute; display: flex; align-items: center; gap: 6px; white-space: nowrap; }
  .contact-bar svg { width: 8px; height: 8px; flex: none; }

  .hotline {
    position: absolute; left: 25px; top: 702px;
    display: flex; align-items: center; gap: 5px;
    font-weight: 700; font-size: 16px; line-height: 20px;
  }
  .hotline__rule { position: absolute; left: 30px; top: 725px; width: 141px; height: 1px; background: var(--red); }
</style>
</head>
<body>
<main class="flyer">
  <svg class="flyer__shapes" width="540" height="764" viewBox="0 0 540 764">
    <defs>
      <clipPath id="photo-clip"><circle cx="381" cy="108" r="227"/></clipPath>
      <linearGradient id="photo-tones" x1="0" y1="0" x2="0" y2="1">
        <stop offset="0" stop-color="#3E8FD6"/>
        <stop offset=".38" stop-color="#7DB6E4"/>
        <stop offset=".5" stop-color="#9A7350"/>
        <stop offset="1" stop-color="#6E4329"/>
      </linearGradient>
      <linearGradient id="bin-tones" x1="0" y1="0" x2="0" y2="1">
        <stop offset="0" stop-color="#E8332D"/>
        <stop offset="1" stop-color="#B81E1C"/>
      </linearGradient>
    </defs>

    <rect class="materials-panel" x="0" y="313" width="540" height="209" fill="var(--panel)"/>

    <g role="img" aria-label="Photo: yellow excavator digging soil at the pit">
      <rect x="150" y="-130" width="460" height="465" fill="url(#photo-tones)" clip-path="url(#photo-clip)"/>
    </g>

    <path d="M 326 -4 A 247 247 0 0 0 286 20" stroke="var(--red)" stroke-width="13" fill="none" stroke-linecap="round"/>
    <path d="M 548 200 A 247 247 0 0 1 467 327" stroke="var(--red)" stroke-width="13" fill="none" stroke-linecap="round"/>

    <path class="hero-blob" d="M 0 130 Q 30 60 129 59 A 128 128 0 0 1 257 187 A 128 128 0 0 1 185 313 L 0 313 Z" fill="var(--red-soft)" opacity=".95"/>

    <circle cx="80" cy="77" r="62" fill="var(--white)"/>
    <circle cx="80" cy="77" r="58" fill="var(--green)"/>

    <circle cx="304" cy="492" r="12.5" fill="#F0203A"/>
    <circle cx="293" cy="509" r="4.5" fill="#F0203A"/>

    <g role="img" aria-label="Photo: red roll-off dumpster">
      <path d="M 0 600 L 194 597 L 192 656 L 176 658 L 20 668 L 0 662 Z" fill="url(#bin-tones)"/>
    </g>
  </svg>

  <div class="brand">Ridgeway<br>Haulers</div>

  <h1 class="headline">Materials<br>Available for<br>Pick Up and/<br>or Delivery</h1>

  <h2 class="section-title" style="left:25px;top:362px"><strong>Recycled</strong> Breaker Run</h2>
  <h2 class="section-title" style="left:321px;top:362px"><strong>Mound</strong> Sand</h2>

  <p class="item" style="left:26px;top:396px"><b>1 1/4"</b> Crushed<br>Recycled Stone</p>
  <p class="item" style="left:26px;top:438px"><b>3/4" &amp; 1 1/4"</b><br>Crushed<br>Recycled<br>Asphalt</p>

  <p class="item" style="left:154px;top:396px"><b>1 1/4"</b> Screened<br>Dig Right On In</p>
  <p class="item" style="left:154px;top:438px"><b>3/4"</b> Clean Stone</p>
  <p class="item" style="left:154px;top:463px"><b>3/8"</b> Washed<br>Pea Stone</p>

  <p class="item" style="left:323px;top:393px"><b>Compost</b></p>
  <p class="item" style="left:323px;top:418px"><b>Topsoil</b></p>
  <p class="item" style="left:323px;top:443px"><b>Fill/Clay</b><br>Fill Material</p>

  <p class="item" style="left:420px;top:393px"><b>Peot Moss</b></p>
  <p class="item" style="left:420px;top:418px"><b>Fill Sand</b><br>Material</p>
  <p class="item" style="left:420px;top:459px"><b>Reclaimed</b><br>Cream City<br>Bricks</p>

  <h2 class="section-title section-title--dumping" style="left:25px;top:537px"><strong>Dumping of<br>Materials</strong> with<br>Approval</h2>

  <p class="item" style="left:210px;top:538px"><b>Brush</b> and /<br><b>or Stumps</b></p>
  <p class="item" style="left:210px;top:580px"><b>Hydro Vac</b><br>Slurry Dumping</p>
  <p class="item" style="left:210px;top:621px"><b>Clean</b> Concrete</p>

  <p class="item" style="left:357px;top:536px"><b>Asphalt</b></p>
  <p class="item" style="left:357px;top:561px"><b>Clean</b> Brick</p>
  <p class="item" style="left:357px;top:586px"><b>Fill</b> Material</p>
  <p class="item" style="left:357px;top:612px"><b>Dirty</b> and / or <b>Large<br>Large Concrete</b><br>or <b>Tolvaran</b></p>

  <div class="hotline">
    <svg width="16" height="16" viewBox="0 0 24 24" fill="none" stroke="var(--red)" stroke-width="1.8" stroke-linejoin="round"><path d="M5 3h4l2 5-2.5 1.5a11 11 0 0 0 6 6L16 13l5 2v4a2 2 0 0 1-2 2A16 16 0 0 1 3 5a2 2 0 0 1 2-2z"/><path d="M15 3a6 6 0 0 1 6 6M15 7a2 2 0 0 1 2 2"/></svg>
    <span>+920 555 0147</span>
  </div>
  <div class="hotline__rule"></div>

  <address class="contact-bar">
    <span class="contact-bar__line" style="left:20px;top:12px">
      <svg viewBox="0 0 10 10"><rect x="0" y="1.5" width="10" height="7" rx="1" fill="var(--red)"/><path d="M0.5 2l4.5 3.5L9.5 2" stroke="#fff" stroke-width="1" fill="none"/></svg>
      dispatch@ridgewayhaulers.com
    </span>
    <span class="contact-bar__line" style="left:20px;top:29px">
      <svg viewBox="0 0 10 10" fill="none" stroke="var(--red)" stroke-width="1"><circle cx="5" cy="5" r="4.4"/><ellipse cx="5" cy="5" rx="2" ry="4.4"/><path d="M0.6 5h8.8"/></svg>
      www.ridgewayhaulers.com
    </span>
    <span class="contact-bar__line" style="left:188px;top:12px">
      <svg viewBox="0 0 10 10"><path d="M1 4a4 2 0 0 1 8 0v1H7V4H3v1H1z M2 6h6l1 3H1z" fill="var(--red)"/></svg>
      920-555-0182
    </span>
    <span class="contact-bar__line" style="left:188px;top:29px">
      <svg viewBox="0 0 10 10"><path d="M5 0.5a3.3 3.3 0 0 0-3.3 3.3C1.7 6.4 5 9.5 5 9.5s3.3-3.1 3.3-5.7A3.3 3.3 0 0 0 5 0.5z" fill="var(--red)"/><circle cx="5" cy="3.8" r="1.2" fill="#fff"/></svg>
      1480 Alder road millbrook, wi 54000
    </span>
  </address>
</main>
</body>
</html>
```